Business Card for beauty technology startup

Design Glimora Business Card for a Beauty, based on the website identity and colors (https://www.glimora-example.com).
Glimora is a beauty tech startup that gathers helpful product info for beauty lovers and consumers (such as availability on stores, price range and product reviews) for makeup products. The card design must be young, colorful but clean, and very modern.

Target Market(s)

woman, 15-35

Industry/Entity Type

Cosmetics

Contact Information for Business Card

Full Name, address, phone

Font styles to use
Other font styles liked:
• Advent Pro

Colors
e34297
86cfc6
ffffff
5c5c5c
e8e8e8
e667a6
b2b2b2

Requirements
Must have
• One full colored side with a creative design and another with card info
• Use Color palette: #95C5C5 and/or #D38AA5
• Use fonts: Advent Pro
• Use website identity: https://www.glimora-example.com
Nice to have
• If needed extra font: Roboto

```html
<!DOCTYPE html>
<html lang="en">
<head>
<meta charset="utf-8">
<title>Glimora Business Card</title>
<link href="https://fonts.googleapis.com/css2?family=Advent+Pro:wght@300;400&family=Roboto:wght@400;500&display=swap" rel="stylesheet">
<style>
  :root {
    --backdrop: #e9e6e3;
    --card-white: #f7f7f6;
    --card-dark: #18181a;
    --rose: #b67b91;
    --rose-text: #a9708a;
    --ink: #5c5c5c;
    --muted: #9a9a9a;
    --ring-faint: #2b2629;
    --url-grey: #4f4d50;
  }
  * { margin: 0; padding: 0; box-sizing: border-box; }
  html, body { width: 1200px; height: 960px; overflow: hidden; }
  body { background: var(--backdrop); position: relative; font-family: "Roboto", Arial, sans-serif; }

  .card {
    position: absolute;
    width: 600px;
    height: 342px;
    border-radius: 18px;
    overflow: hidden;
  }
  .card--front { left: 315px; top: 113px; background: var(--card-white); }
  .card--back { left: 312px; top: 472px; width: 598px; height: 340px; background: var(--card-dark); }

  .front-disc { position: absolute; left: 0; top: 0; }

  .brand {
    position: absolute;
    display: flex;
    align-items: center;
    gap: 22px;
    left: 25px;
    top: 26px;
  }
  .brand__dot {
    width: 50px; height: 50px;
    border: 2px solid var(--rose);
    border-radius: 50%;
  }
  .brand__name {
    font-family: "Advent Pro", "Roboto", sans-serif;
    font-weight: 300;
    font-size: 40px;
    letter-spacing: 5px;
    color: var(--rose-text);
    line-height: 1;
  }

  .holder { position: absolute; left: 28px; top: 131px; }
  .holder__name { font-size: 19px; font-weight: 500; color: var(--rose-text); letter-spacing: 0.3px; }
  .holder__role { font-size: 14px; color: var(--muted); margin-top: 5px; }

  .address { position: absolute; left: 28px; top: 192px; font-size: 14px; line-height: 19px; color: var(--ink); }

  .contacts { position: absolute; left: 28px; top: 239px; list-style: none; font-size: 14px; color: var(--ink); }
  .contacts li { display: flex; align-items: center; height: 19px; }
  .contacts svg { width: 13px; height: 13px; margin-right: 10px; fill: var(--rose); }

  .back-ring { position: absolute; left: 0; top: 0; }
  .back-name {
    position: absolute;
    right: 32px;
    top: 246px;
    font-family: "Advent Pro", "Roboto", sans-serif;
    font-weight: 300;
    font-size: 50px;
    letter-spacing: 5px;
    color: var(--rose);
    line-height: 1;
  }
  .back-url {
    position: absolute;
    right: 32px;
    top: 301px;
    font-size: 12px;
    letter-spacing: 3.4px;
    color: var(--url-grey);
  }
</style>
</head>
<body>
  <section class="card card--front">
    <svg class="front-disc" width="600" height="342" viewBox="0 0 600 342" aria-hidden="true">
      <circle cx="428" cy="185" r="172" fill="var(--rose)"/>
    </svg>
    <div class="brand">
      <span class="brand__dot"></span>
      <span class="brand__name">GLIMORA</span>
    </div>
    <div class="holder">
      <p class="holder__name">MARA ELLISON</p>
      <p class="holder__role">CEO/FOUNDER</p>
    </div>
    <p class="address">1420 Willowbend Court<br>Fairview, Oregon 97024</p>
    <ul class="contacts">
      <li><svg viewBox="0 0 16 16"><path d="M3.5 1l2.5 3-1.5 2a9 9 0 0 0 5 5l2-1.5 3 2.5-1.5 3C7 15 1 9 .5 3.5z"/></svg>555 204 7731</li>
      <li><svg viewBox="0 0 16 16"><path d="M4 0h8v16H4zM5.5 2v10h5V2zM7 13.2h2v1.4H7z" fill-rule="evenodd"/></svg>555 318 6042</li>
      <li><svg viewBox="0 0 16 16"><path d="M4 1h8v4H4zM1 6h14v6h-2v3H3v-3H1zM5 10v3.5h6V10z" fill-rule="evenodd"/></svg>555 472 0915</li>
      <li><svg viewBox="0 0 16 16"><path d="M1 3h14v10H1zM2.5 4.5 8 9l5.5-4.5z" fill-rule="evenodd"/></svg>info@glimora-example.com</li>
    </ul>
  </section>

  <section class="card card--back">
    <svg class="back-ring" width="598" height="340" viewBox="0 0 598 340" aria-hidden="true">
      <circle cx="170" cy="178" r="158" fill="none" stroke="var(--ring-faint)" stroke-width="4"/>
    </svg>
    <p class="back-name">GLIMORA</p>
    <p class="back-url">www.glimora-example.com</p>
  </section>
</body>
</html>
```